Gooey Tides

I am creating an online slime shop that will sell handmade custom slimes. I need to be able to have payment/shipping options and the ability to change product photos since the product and product name will change often

Target Market(s)

Slime

Industry/Entity Type

Retail - online sales

Coding

Coded - Design and coding required

Number of Pages Required

2 page

Font styles to use
Sans Serif

Colors
0094D4
00A9DD
6FCCEA
C7EBF8
E9F6FB
E54698
E96AAD
F1A4CE
F9D9EA
FCEFF6
A7469A
B969AE
D3A5CF
EDDBEB
F8F0F9

Requirements
Must have
• My logo, my domain, ability to change photos of products for sale, payment options, shipping options, social media links, contact us,

```html
<!DOCTYPE html>
<html lang="en">
<head>
<meta charset="utf-8">
<title>Gooey Tides – Handmade Custom Slimes</title>
<link href="https://fonts.googleapis.com/css2?family=Poppins:wght@400;500;600;700&family=Lato:wght@400;700&display=swap" rel="stylesheet">
<style>
:root{
  --purple:#9a35b8;
  --purple-deep:#7e2cc2;
  --violet-footer:#9233cc;
  --pink-band:#c44a8c;
  --lavender:#f5eefb;
  --ink:#222;
  --body:#3a3a3a;
  --muted:#666;
  --line:#e6dbe9;
  --white:#fff;
  --star:#f2a900;
  --heart:#f0565e;
}
*{box-sizing:border-box;margin:0;padding:0}
html,body{width:1200px;height:4563px;overflow:hidden;background:var(--white)}
body{position:relative;font-family:"Lato",sans-serif;color:var(--body)}
.abs{position:absolute}
.heading{font-family:"Poppins",sans-serif;font-weight:600;color:var(--purple);text-align:center;font-size:35px;letter-spacing:.3px;width:1200px;left:0}
.mark{position:absolute;left:584px;width:32px;height:32px;border-radius:50%;border:3px solid #222;background:#fff}
.btn{position:absolute;display:flex;align-items:center;justify-content:center;gap:8px;font-family:"Poppins",sans-serif;font-weight:600;font-size:15px;color:#fff;border-radius:30px;background:linear-gradient(90deg,var(--purple),var(--purple-deep));box-shadow:0 4px 10px rgba(122,44,194,.25)}
.btn .dot{width:14px;height:14px;border-radius:50%;border:2px solid #fff}
/* header */
.topline{top:0;left:0;width:1200px;height:4px;background:linear-gradient(90deg,var(--pink-band),var(--purple-deep))}
.call{top:42px;left:112px;display:flex;align-items:center;gap:8px;font-family:"Poppins",sans-serif;font-weight:600;font-size:13px;color:var(--ink)}
.call .ico{width:20px;height:20px}
.nav a{position:absolute;top:102px;font-family:"Poppins",sans-serif;font-size:14px;color:#777;text-decoration:none;letter-spacing:.3px}
.nav a.active{color:var(--purple-deep);font-weight:500}
.nav a.active::after{content:"";position:absolute;left:0;right:0;bottom:-5px;height:2px;background:var(--purple-deep)}
.icons span{position:absolute;top:34px;width:32px;height:32px;border-radius:8px;border:1px solid #ccc;display:flex;align-items:center;justify-content:center;background:#fff}
.badge{position:absolute;top:-6px;right:-4px;width:12px;height:12px;border-radius:50%;background:var(--purple-deep)}
.brand{top:10px;left:506px;width:188px;height:168px;border-radius:0 0 94px 94px;background:#fff;display:flex;align-items:center;justify-content:center;gap:8px;z-index:3}
.brand .circ{width:14px;height:14px;border-radius:50%;background:var(--purple)}
.brand b{font-family:"Poppins",sans-serif;font-weight:700;font-size:22px;color:var(--purple)}
/* hero */
.hero{top:145px;left:0;width:1200px;height:560px;background:linear-gradient(160deg,#2c4a35 0%,#3f7a4d 35%,#5fc29a 70%,#7fdcc0 100%)}
.hero h1{position:absolute;top:120px;left:112px;font-family:"Poppins",sans-serif;font-weight:400;font-size:48px;line-height:69px;color:#fff;letter-spacing:.5px}
.hero h1 strong{font-weight:700}
.hero p{position:absolute;top:262px;left:112px;width:380px;font-size:14px;line-height:30px;color:#fff}
.shop-now{position:absolute;top:376px;left:113px;width:158px;height:50px;border-radius:30px;background:#fff;display:flex;align-items:center;justify-content:center;gap:8px;font-family:"Poppins",sans-serif;font-weight:600;font-size:15px;color:var(--purple-deep)}
.shop-now .dot{width:16px;height:16px;border-radius:50%;border:2px solid var(--ink)}
.dots{position:absolute;top:458px;left:574px;display:flex;gap:14px}
.dots i{width:6px;height:6px;border-radius:50%;background:rgba(255,255,255,.6)}
.dots i.on{background:#fff}
/* welcome */
.welcome p{position:absolute;left:170px;width:860px;text-align:center;font-size:14.5px;line-height:31px;color:var(--body)}
/* products band */
.band{top:1260px;left:0;width:1200px;height:480px}
.tab{position:absolute;top:1427px;height:50px;border-radius:30px;display:flex;align-items:center;justify-content:center;font-family:"Poppins",sans-serif;font-weight:600;font-size:15px}
.tab.on{left:378px;width:182px;background:#fff;color:var(--purple-deep)}
.tab.off{left:588px;width:233px;border:2px solid #fff;color:#fff}
.pcard{position:absolute;top:1533px;width:229px;height:337px;background:#fff;border-radius:10px;box-shadow:0 4px 14px rgba(0,0,0,.12);padding:9px}
.pcard .ph{width:211px;height:204px;border-radius:8px}
.pcard .row{display:flex;justify-content:space-between;align-items:center;margin-top:12px}
.pcard .name{font-size:14px;color:var(--ink)}
.pcard .buy{width:90px;height:32px;border-radius:20px;background:linear-gradient(90deg,var(--purple),var(--purple-deep));color:#fff;font-family:"Poppins",sans-serif;font-weight:600;font-size:11px;display:flex;align-items:center;justify-content:center}
.pcard .stars{color:var(--star);font-size:12px;letter-spacing:1px;margin-top:-6px}
.pcard .desc{font-size:11px;line-height:23px;color:#555;margin-top:6px}
.arrow{position:absolute;top:1750px;width:20px;height:20px;border-radius:50%;background:#111;display:flex;align-items:center;justify-content:center}
/* custom products */
.ccard{position:absolute;top:2088px;width:310px}
.ccard .ph{width:310px;height:362px;position:relative}
.ccard .heart{position:absolute;top:18px;right:18px}
.ccard h3{margin-top:32px;text-align:center;font-family:"Poppins",sans-serif;font-weight:500;font-size:16px;color:var(--ink)}
.ccard a{display:block;margin-top:10px;text-align:center;font-family:"Poppins",sans-serif;font-weight:600;font-size:12px;color:var(--purple-deep);text-decoration:underline}
/* contact */
.contact{top:2710px;left:112px;width:978px;height:756px;background:var(--lavender);border-radius:30px}
.field{position:absolute;background:#fff;border-radius:6px;box-shadow:0 2px 6px rgba(120,80,160,.12);font-size:12.5px;color:#888;padding:18px 18px}
.panda-art{top:3297px;left:434px;width:328px;height:177px;border-radius:50% 50% 10px 10px;background:radial-gradient(ellipse at 50% 55%,#d9dcd8 0%,#eef1ec 50%,rgba(245,238,251,0) 75%)}
/* news */
.ncard{position:absolute;top:3658px;width:309px;height:394px;border:1.5px dashed #d98aa8;border-radius:14px;padding:18px 19px}
.ncard .ph{width:271px;height:192px;border-radius:10px}
.ncard h4{margin-top:28px;font-family:"Poppins",sans-serif;font-weight:500;font-size:14px;line-height:27px;color:var(--ink)}
.ncard p{font-size:12.5px;line-height:27px;color:#666}
.ncard a{display:block;margin-top:6px;font-family:"Poppins",sans-serif;font-size:12.5px;color:var(--pink-band);text-decoration:underline}
/* footer */
.footer{top:4110px;left:0;width:1200px;height:453px}
.f-brand{top:4270px;left:112px;display:flex;align-items:center;gap:10px}
.f-brand .circ{width:16px;height:16px;border-radius:50%;background:#fff}
.f-brand b{font-family:"Poppins",sans-serif;font-weight:700;font-size:30px;color:#fff}
.f-mail{top:4398px;left:112px;display:flex;align-items:center;gap:12px;color:#fff;font-family:"Poppins",sans-serif;font-size:14px}
.fcol{position:absolute;top:4243px;color:#fff}
.fcol h5{font-family:"Poppins",sans-serif;font-weight:600;font-size:15px;margin-bottom:10px}
.fcol li{list-style:none;font-size:13px;line-height:31px}
.news-in{top:4282px;left:833px;width:255px;height:32px;border:1.5px solid #fff;border-radius:20px;color:#fff;font-size:11px;padding:8px 22px}
.sub{top:4334px;left:833px;width:135px;height:39px;border-radius:22px;background:#fff;color:var(--purple-deep);font-family:"Poppins",sans-serif;font-weight:600;font-size:12px;display:flex;align-items:center;justify-content:center}
.divider{top:4470px;left:112px;width:976px;height:1px;background:rgba(255,255,255,.45)}
.copy{top:4514px;left:112px;color:#fff;font-size:14px}
.pay{top:4511px;left:812px;display:flex;gap:8px}
.pay i{width:39px;height:27px;border-radius:4px;background:#fff;opacity:.92}
</style>
</head>
<body>

<!-- header -->
<div class="abs topline"></div>
<div class="abs call">
  <svg class="ico" viewBox="0 0 24 24"><path d="M6.6 10.8a15 15 0 0 0 6.6 6.6l2.2-2.2a1 1 0 0 1 1-.25 11.4 11.4 0 0 0 3.6.57 1 1 0 0 1 1 1V20a1 1 0 0 1-1 1A17 17 0 0 1 3 4a1 1 0 0 1 1-1h3.5a1 1 0 0 1 1 1c0 1.25.2 2.45.57 3.57a1 1 0 0 1-.25 1z" fill="#222"/></svg>
  CALL US: +1 555 014 2290
</div>
<nav class="nav">
  <a class="active" style="left:112px">HOME</a>
  <a style="left:248px">PRODUCTS</a>
  <a style="left:418px">ABOUT</a>
  <a style="left:734px">ARRIVALS</a>
  <a style="left:893px">BLOG</a>
  <a style="left:1012px">CONTACT</a>
</nav>
<div class="icons">
  <span style="left:952px"><svg width="13" height="13" viewBox="0 0 24 24"><circle cx="10" cy="10" r="6.5" fill="none" stroke="#333" stroke-width="2.5"/><path d="M15 15l6 6" stroke="#333" stroke-width="2.5"/></svg></span>
  <span style="left:1003px"><svg width="14" height="14" viewBox="0 0 24 24"><path d="M12 20s-8-5-8-10.5A4.5 4.5 0 0 1 12 7a4.5 4.5 0 0 1 8 2.5C20 15 12 20 12 20z" fill="none" stroke="#333" stroke-width="2.2"/></svg><i class="badge"></i></span>
  <span style="left:1055px"><svg width="13" height="13" viewBox="0 0 24 24"><circle cx="12" cy="8" r="4.5" fill="none" stroke="#333" stroke-width="2.2"/><path d="M4 21c1-4.5 4-6.5 8-6.5s7 2 8 6.5" fill="none" stroke="#333" stroke-width="2.2"/></svg></span>
</div>
<div class="abs brand"><span class="circ"></span><b>Gooey Tides</b></div>

<!-- hero -->
<section class="abs hero" role="img" aria-label="Photo of a mint green slime with a mossy garden scene, a small tree and two toy pandas">
  <h1>WE SELL <strong>HANDMADE</strong><br><strong>CUSTOM SLIMES</strong></h1>
  <p>Lorem ipsum dolor sit amet, consectetur adipiscing elit, sed do eiusmod tempor incididunt ut labore et dolore magna aliqua.</p>
  <div class="shop-now"><span class="dot"></span>SHOP NOW</div>
  <div class="dots"><i></i><i class="on"></i><i></i></div>
  <svg class="abs" style="left:0;bottom:0" width="1200" height="70" viewBox="0 0 1200 70" preserveAspectRatio="none"><path d="M0 40 C60 20 110 20 160 36 S260 60 330 44 S450 18 530 36 S660 62 740 44 S870 14 960 34 S1080 60 1140 34 S1190 18 1200 22 L1200 70 L0 70Z" fill="#fff"/></svg>
</section>

<!-- welcome -->
<section class="welcome">
  <span class="mark" style="top:780px"></span>
  <h2 class="abs heading" style="top:826px">WELCOME TO GOOEY TIDES</h2>
  <p style="top:896px">Lorem ipsum dolor sit amet, consectetur adipiscing elit, sed do eiusmod tempor incididunt ut labore et dolore magna aliqua. Ut enim ad minim veniam, quis nostrud exercitation ullamco laboris nisi ut aliquip ex ea commodo consequat.&nbsp; enim ad minim veniam, quis nostrud exercitation ullamco laboris nisi ut aliquip ex ea commodo consequat.</p>
  <p style="top:1018px">Duis aute irure dolor in reprehenderit in voluptate velit esse cillum dolore eu fugiat nulla pariatur. Excepteur sint occaecat cupidatat non proident, sunt in culpa qui officia deserunt mollit anim id est laborum</p>
  <div class="btn" style="top:1117px;left:521px;width:158px;height:50px"><span class="dot"></span>VIEW MORE</div>
</section>

<!-- our products -->
<section>
  <svg class="abs band" viewBox="0 0 1200 480" preserveAspectRatio="none"><path d="M0 0H1200V430 C1140 400 1090 470 1030 450 S900 400 820 440 S680 470 600 440 S460 400 380 440 S230 470 160 440 S40 400 0 430Z" fill="#c44a8c"/></svg>
  <span class="mark" style="top:1310px;border-color:#fff;background:transparent"></span>
  <h2 class="abs heading" style="top:1360px;color:#fff">OUR PRODUCTS</h2>
  <div class="tab on">NEW ARRIVALS</div>
  <div class="tab off">FEATURED PRODUCTS</div>

  <div class="arrow" style="left:34px"><svg width="10" height="10" viewBox="0 0 10 10"><path d="M6.5 1.5L3 5l3.5 3.5" stroke="#fff" stroke-width="1.8" fill="none"/></svg></div>
  <div class="arrow" style="left:1142px"><svg width="10" height="10" viewBox="0 0 10 10"><path d="M3.5 1.5L7 5 3.5 8.5" stroke="#fff" stroke-width="1.8" fill="none"/></svg></div>

  <article class="pcard" style="left:92px">
    <div class="ph" role="img" aria-label="Product photo: mint slime garden with moss, tree and toy pandas" style="background:linear-gradient(170deg,#4a5a48,#5aa86a 45%,#6fe0b2)"></div>
    <div class="row"><span class="name">Gooey Tides</span><span class="buy">BUY NOW</span></div>
    <div class="stars">★★★★★</div>
    <p class="desc">Excepteur sint occaecat cupidatat non proident, sunt in culpa qui officia</p>
  </article>
  <article class="pcard" style="left:355px">
    <div class="ph" role="img" aria-label="Product photo: jar of pastel layered slime with cat figures on top" style="background:linear-gradient(180deg,#f08aa0,#f4c2a8 45%,#8fc6e6 75%,#e7b2cc)"></div>
    <div class="row"><span class="name">Gooey Tides</span><span class="buy">BUY NOW</span></div>
    <div class="stars">★★★★★</div>
    <p class="desc">Excepteur sint occaecat cupidatat non proident, sunt in culpa qui officia</p>
  </article>
  <article class="pcard" style="left:615px">
    <div class="ph" role="img" aria-label="Product photo: jar of pink waffle textured slime with sprinkles" style="background:linear-gradient(180deg,#d85c7a,#f3a0a8 45%,#e66fbf 80%,#c455a6)"></div>
    <div class="row"><span class="name">Gooey Tides</span><span class="buy">BUY NOW</span></div>
    <div class="stars">★★★★★</div>
    <p class="desc">Excepteur sint occaecat cupidatat non proident, sunt in culpa qui officia</p>
  </article>
  <article class="pcard" style="left:877px">
    <div class="ph" role="img" aria-label="Product photo: clear slime jar with glitter charms and panda toys" style="background:linear-gradient(180deg,#f0a6c8,#c9c6d4 45%,#8fa0b8 80%,#d9b6d8)"></div>
    <div class="row"><span class="name">Gooey Tides</span><span class="buy">BUY NOW</span></div>
    <div class="stars">★★★★★</div>
    <p class="desc">Excepteur sint occaecat cupidatat non proident, sunt in culpa qui officia</p>
  </article>
</section>

<!-- custom products -->
<section>
  <span class="mark" style="top:1955px"></span>
  <h2 class="abs heading" style="top:2001px">CUSTOM PRODUCTS</h2>
  <article class="ccard" style="left:112px">
    <div class="ph" role="img" aria-label="Photo of a turquoise slime with lily pads and tiny flowers" style="background:radial-gradient(ellipse 42% 30% at 50% 48%,#2fb1d8 0%,#2aa8d0 80%,#ededed 100%)">
      <svg class="heart" width="18" height="16" viewBox="0 0 24 21"><path d="M12 21S0 13.5 0 6.5A6 6 0 0 1 12 3a6 6 0 0 1 12 3.5C24 13.5 12 21 12 21z" fill="#f0565e"/></svg>
    </div>
    <h3>Custom Slimes</h3><a>SHOP NOW</a>
  </article>
  <article class="ccard" style="left:445px">
    <div class="ph" role="img" aria-label="Photo of a deep blue glitter slime with a small duck charm" style="background:radial-gradient(ellipse 42% 30% at 50% 50%,#1f77a8 0%,#1a6ea0 80%,#ededed 100%)">
      <svg class="heart" width="18" height="16" viewBox="0 0 24 21"><path d="M12 21S0 13.5 0 6.5A6 6 0 0 1 12 3a6 6 0 0 1 12 3.5C24 13.5 12 21 12 21z" fill="#f0565e"/></svg>
      <svg class="abs" style="top:52px;right:18px" width="16" height="16" viewBox="0 0 24 24"><circle cx="18" cy="5" r="3" fill="#222"/><circle cx="6" cy="12" r="3" fill="#222"/><circle cx="18" cy="19" r="3" fill="#222"/><path d="M8.6 10.5l6.8-4M8.6 13.5l6.8 4" stroke="#222" stroke-width="2"/></svg>
    </div>
    <h3>Custom Slimes</h3><a>SHOP NOW</a>
  </article>
  <article class="ccard" style="left:780px">
    <div class="ph" role="img" aria-label="Photo of a glossy amber orange slime puddle" style="background:radial-gradient(ellipse 35% 30% at 50% 50%,#f0a222 0%,#e08a12 75%,#f7f7f7 100%)">
      <svg class="heart" width="18" height="16" viewBox="0 0 24 21"><path d="M12 21S0 13.5 0 6.5A6 6 0 0 1 12 3a6 6 0 0 1 12 3.5C24 13.5 12 21 12 21z" fill="#f0565e"/></svg>
    </div>
    <h3>Custom Slimes</h3><a>SHOP NOW</a>
  </article>
  <div class="btn" style="top:2582px;left:521px;width:158px;height:50px"><span class="dot"></span>BUY NOW</div>
</section>

<!-- contact -->
<section>
  <div class="abs contact"></div>
  <span class="mark" style="top:2779px"></span>
  <h2 class="abs heading" style="top:2825px">GET IN TOUCH WITH US</h2>
  <div class="field" style="top:2905px;left:166px;width:426px;height:53px">First Name</div>
  <div class="field" style="top:2905px;left:609px;width:428px;height:53px">Last Name</div>
  <div class="field" style="top:2976px;left:166px;width:426px;height:53px">Email</div>
  <div class="field" style="top:2976px;left:609px;width:428px;height:53px">Phone Number</div>
  <div class="field" style="top:3047px;left:166px;width:871px;height:122px">Message</div>
  <div class="btn" style="top:3219px;left:522px;width:158px;height:49px"><span class="dot"></span>SUBMIT</div>
  <div class="abs panda-art" role="img" aria-label="Watercolour illustration of a panda sitting among bamboo leaves"></div>
</section>

<!-- news -->
<section>
  <span class="mark" style="top:3538px"></span>
  <h2 class="abs heading" style="top:3584px;color:var(--pink-band)">LATEST NEWS</h2>
  <article class="ncard" style="left:112px">
    <div class="ph" role="img" aria-label="Photo of hands stretching red slime from a jar" style="background:linear-gradient(135deg,#f3d4d0,#f0455a 45%,#e52a44 70%,#f4c8c4)"></div>
    <h4>Duis aute irure dolor in reprehenderit in voluptate velit esse cillum</h4>
    <p>Excepteur sint occaecat cupidatat non qui deserunt mollit anim id est laborum.</p>
    <a>Read More</a>
  </article>
  <article class="ncard" style="left:445px">
    <div class="ph" role="img" aria-label="Photo of hands stretching purple and blue glitter slime" style="background:linear-gradient(135deg,#e8c6e4,#7a6ad6 45%,#4fa0e0 70%,#f0f0f4)"></div>
    <h4>Exercitation ullamco laboris nisi ut aliquo consequat</h4>
    <p>Excepteur sint occaecat cupidatat non qui deserunt mollit anim id est laborum.</p>
    <a>Read More</a>
  </article>
  <article class="ncard" style="left:778px">
    <div class="ph" role="img" aria-label="Photo of a child playing with pink glitter slime" style="background:linear-gradient(135deg,#9a8c84,#e6a3bd 40%,#e54b9e 65%,#f2d6e2)"></div>
    <h4>Lorem ipsum dolor sit amet, csecter adipiscing elit tempor</h4>
    <p>Excepteur sint occaecat cupidatat non qui deserunt mollit anim id est labrum.</p>
    <a>Read More</a>
  </article>
</section>

<!-- footer -->
<footer>
  <svg class="abs footer" viewBox="0 0 1200 453" preserveAspectRatio="none"><path d="M0 30 C70 50 140 58 220 40 S360 0 440 22 S560 60 640 40 S780 0 860 26 S1000 62 1080 36 S1170 10 1200 16 V453 H0Z" fill="#9233cc"/></svg>
  <div class="abs f-brand"><span class="circ"></span><b>Gooey Tides</b></div>
  <div class="abs f-mail">
    <svg width="18" height="13" viewBox="0 0 18 13"><rect width="18" height="13" rx="1.5" fill="#fff"/><path d="M1 1.5l8 6 8-6" stroke="#9233cc" stroke-width="1.6" fill="none"/></svg>
    hello@gooeytides.com
  </div>
  <div class="fcol" style="left:386px"><h5>LINKS</h5><ul><li>Contact Us</li><li>About Us</li><li>Product</li><li>Testimonials</li><li>Home</li></ul></div>
  <div class="fcol" style="left:539px"><h5>POLICY</h5><ul><li>Return Policy</li><li>Terms Of Use</li><li>Security</li><li>Privacy Policy</li><li>Sitemap</li></ul></div>
  <div class="fcol" style="left:688px"><h5>HELP</h5><ul><li>Term &amp; policy</li><li>Delivery</li></ul></div>
  <div class="fcol" style="left:833px"><h5>SIGN UP TO OUR NEWSLETTER</h5></div>
  <div class="abs news-in">Enter the email</div>
  <div class="abs sub">SUBSCRIBE US</div>
  <div class="abs divider"></div>
  <div class="abs copy">Copyrights@2024.Gooey Tides All Rights Reserved</div>
  <div class="abs pay" aria-label="Accepted payment methods"><i></i><i></i><i></i><i></i><i></i><i></i></div>
</footer>

</body>
</html>
```